Sales presentation introduction for Finance and Tech firms

Our business is two fold - 1) recruitment 2) consultancy. We would like a one or two page template that we can use to send to potential clients. The template will ideally be the same for the recruitment and consultancy side. We need to be able to edit the template to enter text.

I have attached our logo so you can see what we currently use on Corvella.

Sector is financial services and technology. We do not intent to have lots of text but the layout/images/designs to be used should cover some of page in a way that it takes up some space to avoid having to write lot of text.

Open to colour suggestions.

Please look at the attached word doc to see the text I would like for the two presentations.

Happy to answer questions.

Target Market(s)

Directors

Industry/Entity Type

Finance and tech companies

Colors
0094D4
00A9DD
6FCCEA
C7EBF8
E9F6FB

Requirements
Must have
• Editable text

```html
<!DOCTYPE html>
<html lang="en">
<head>
<meta charset="utf-8">
<title>Veltrix – Consultancy &amp; Recruitment Sheets</title>
<link href="https://fonts.googleapis.com/css2?family=Jost:wght@300;400;600;700&family=Montserrat:wght@800&family=Open+Sans:ital,wght@1,800&family=Arimo:wght@400&display=swap" rel="stylesheet">
<style>
:root{
  --board:#1c1d1f;
  --deep:#1b5aa2;
  --brand:#2a7ccb;
  --sky:#6fccea;
  --ice:#e9f6fb;
  --ink:#1f2328;
  --grey:#6b6f75;
  --white:#ffffff;
}
*{margin:0;padding:0;box-sizing:border-box}
html,body{width:1108px;height:1200px;overflow:hidden;background:var(--board)}
.sheet{position:absolute;width:665px;height:861px;transform:scale(.6);transform-origin:0 0;overflow:hidden;font-family:"Arimo",Arial,sans-serif}
.sheet--consult{left:141.6px;top:67.2px}
.sheet--services-a{left:567.6px;top:67.2px}
.sheet--recruit{left:141.6px;top:617.4px}
.sheet--services-b{left:567.6px;top:617.4px}

/* front sheets */
.front{background:var(--white)}
.hero-photo{position:absolute;left:0;top:0;width:665px;height:410px;
  background:
   linear-gradient(180deg,rgba(255,255,255,0) 78%,#fff 100%),
   radial-gradient(ellipse 260px 190px at 70px 60px,rgba(255,255,255,1) 0%,rgba(255,255,255,.6) 55%,rgba(255,255,255,0) 100%),
   linear-gradient(90deg,#dbe8f5 0%,#c6daef 30%,#9fb8de 48%,#5d74aa 62%,#3f558f 72%,#8a6a78 82%,#c77a55 88%,#dfe9f4 100%)}
.hero-band{position:absolute;left:0;top:223px;width:665px;height:149px;
  background:linear-gradient(90deg,var(--deep) 0%,var(--deep) 48%,rgba(27,90,162,.55) 68%,rgba(27,90,162,0) 90%)}
.tagline{position:absolute;left:61px;top:237px;width:270px;color:var(--white);
  font:italic 800 16.5px/19.8px "Open Sans",sans-serif}
.word{position:absolute;color:var(--white);font-family:"Jost",sans-serif;white-space:nowrap;line-height:1}
.word--thin{font-weight:300;opacity:.9}
.word--bold{font-weight:700}
.logo{position:absolute;display:flex;flex-direction:column;align-items:center;gap:10px}
.logo__mark{width:56px;height:56px;background:var(--brand)}
.logo__name{font:400 34px/1 "Jost",sans-serif;color:var(--grey);letter-spacing:.5px}
.front .logo{left:32px;top:24px}
.title{position:absolute;font-family:"Jost",sans-serif;line-height:1}
.title__top{display:block;font-weight:400;font-size:33px;color:var(--ink)}
.title__main{display:block;font-weight:700;font-size:35px;color:var(--deep);letter-spacing:.5px}
.copy{position:absolute;color:var(--ink);font-size:12.4px;line-height:16px}
.copy p+p{margin-top:10px}
.ticks{position:absolute;list-style:none;font-size:12.4px;line-height:16.2px;color:var(--ink)}
.ticks li::before{content:"\2713";display:inline-block;width:20px;color:var(--ink);font-family:"Arimo",Arial,sans-serif}
.footer{position:absolute;left:0;bottom:0;width:665px;height:70px;background:var(--deep)}
.footer .logo{left:286px;top:14px;gap:4px}
.footer .logo__mark{width:18px;height:18px;background:var(--white)}
.footer .logo__name{font-size:13px;color:var(--white)}
.contact{position:absolute;color:var(--white);font-size:11.5px;display:flex;align-items:center;gap:6px;white-space:nowrap}
.contact svg{width:11px;height:11px}

/* recruitment body */
.rcol{position:absolute;font-size:11px;line-height:13.4px;color:var(--ink)}
.rcol p+p{margin-top:10px}
.rcol ul{list-style:none;margin:2px 0 10px}
.rcol li{padding-left:18px;position:relative}
.rcol li::before{content:"";position:absolute;left:3px;top:5px;width:5px;height:5px;border-radius:50%;background:var(--ink)}

/* services sheets */
.services{background:linear-gradient(180deg,#2476c5 0%,#2b82d1 60%,#3a8fd8 100%)}
.services .logo{left:44px;top:30px;gap:12px}
.services .logo__mark{width:50px;height:50px;background:var(--white)}
.services .logo__name{color:var(--white);font-size:31px}
.rule{position:absolute;left:184px;top:110px;width:370px;height:1px;background:rgba(255,255,255,.6)}
.services-photo{position:absolute;left:0;top:560px;width:665px;height:301px;
  background:
   linear-gradient(180deg,rgba(43,130,209,1) 0%,rgba(43,130,209,.4) 40%,rgba(43,130,209,0) 70%),
   linear-gradient(90deg,#c9a8c9 0%,#8fb3e0 25%,#5c8fcf 50%,#a6c3e6 75%,#7aa3d8 100%)}
.service{position:absolute;left:184px;width:375px;color:var(--white)}
.service h3{font:800 12.5px/16px "Montserrat",sans-serif;margin-bottom:3px}
.service h3.service__lead{font-size:15px;line-height:18px}
.service p{font-size:12.4px;line-height:16.1px}
.icon{position:absolute;left:108px;width:46px;height:46px}
</style>
</head>
<body>

<!-- Consultancy front -->
<section class="sheet sheet--consult front">
  <div class="hero-photo" role="img" aria-label="Business people walking past financial charts"></div>
  <span class="word word--bold" style="left:294px;top:24px;font-size:40px">FIXED</span>
  <span class="word word--bold" style="left:294px;top:59px;font-size:40px">INCOME</span>
  <span class="word word--thin" style="left:188px;top:92px;font-size:52px">LEDGER</span>
  <span class="word word--thin" style="left:58px;top:140px;font-size:24px">WORKFLOW <b style="font-weight:700">MIS</b></span>
  <span class="word word--thin" style="left:128px;top:160px;font-size:24px">MANAGEMENT</span>
  <span class="word word--bold" style="left:338px;top:136px;font-size:64px">EQUITY</span>
  <span class="word word--thin" style="left:2px;top:192px;font-size:28px">TRADING PLATFORMS<b style="font-weight:700">XML</b></span>
  <div class="hero-band"></div>
  <p class="tagline">A partner who brings new and innovative ideas to the table, through extensive industry experience and knowledge. Veltrix will ensure you are prepared for growth.</p>
  <div class="logo"><span class="logo__mark"></span><span class="logo__name">VELTRIX</span></div>
  <h1 class="title" style="left:84px;top:416px"><span class="title__top">VELTRIX</span><span class="title__main">CONSULTANCY</span></h1>
  <div class="copy" style="left:85px;top:508px;width:505px">
    <p>Veltrix E2E is a bespoke consultancy firm that specialises in buy side investment. Through an industry based consultative approach we assist our clients in preparing for, and facilitating, long term growth. Working closely with our clients we combine innovative thinking and breakthrough technologies to accelerate progress and, together, achieve enduring results.</p>
    <p>Experienced in successfully delivering change for global organisations as well as assisting smaller firms during their growth phase. Veltrix will work with you create a workable model and ensure successful delivery of the project.</p>
  </div>
  <ul class="ticks" style="left:112px;top:648px">
    <li>Order Management and Trading</li>
    <li>Investment and Research</li>
    <li>Static, Pricing and Benchmark Data</li>
    <li>CRM/ Onboarding</li>
    <li>Performance, Risk and Attribution</li>
  </ul>
  <ul class="ticks" style="left:349px;top:648px">
    <li>Client and Regulatory Reporting</li>
    <li>Compliance</li>
    <li>Finance and Accounting</li>
    <li>Middle and Back Office</li>
  </ul>
  <footer class="footer">
    <div class="logo"><span class="logo__mark"></span><span class="logo__name">VELTRIX</span></div>
    <span class="contact" style="left:368px;top:17px"><svg viewBox="0 0 12 12"><circle cx="6" cy="6" r="6" fill="#fff"/><path d="M6 3a2 2 0 0 0-2 2c0 1.5 2 4 2 4s2-2.5 2-4a2 2 0 0 0-2-2z" fill="#1b5aa2"/></svg>12 Harbor Lane, Sampleton, NJ 12345</span>
    <span class="contact" style="left:368px;top:37px"><svg viewBox="0 0 12 12"><circle cx="6" cy="6" r="6" fill="#fff"/><path d="M4 3l1 .2.5 1.5-.7.6a4 4 0 0 0 1.9 1.9l.6-.7 1.5.5L9 8c-.3.6-1 .9-1.7.6A6 6 0 0 1 3.4 4.7C3.1 4 3.4 3.3 4 3z" fill="#1b5aa2"/></svg>555-014-2290</span>
    <span class="contact" style="left:464px;top:37px"><svg viewBox="0 0 12 12"><circle cx="6" cy="6" r="6" fill="#fff"/><path d="M3 6l6-3-2 6-1.2-2z" fill="#1b5aa2"/></svg>hello@veltrix.co</span>
  </footer>
</section>

<!-- Services reverse A -->
<section class="sheet sheet--services-a services">
  <div class="services-photo" role="img" aria-label="Colleagues talking by an office window with rising arrow graphics"></div>
  <div class="logo"><span class="logo__mark"></span><span class="logo__name">VELTRIX</span></div>
  <div class="rule"></div>
  <svg class="icon" style="top:178px" viewBox="0 0 46 46" fill="none" stroke="#fff" stroke-width="2"><circle cx="23" cy="12" r="7"/><path d="M20 20h6M20 23h6"/><circle cx="9" cy="32" r="3"/><circle cx="23" cy="32" r="3"/><circle cx="37" cy="32" r="3"/><path d="M4 42c0-4 10-4 10 0M18 42c0-4 10-4 10 0M32 42c0-4 10-4 10 0"/></svg>
  <div class="service" style="top:150px"><h3 class="service__lead">Business Strategy</h3><p>Veltrix will help you create a business strategy tailored to your requirements. Ensuing each business process is defined and taken into account allows for a successful design. Creating and implementing an operating model that takes into account budget, resources, culture and your company's vision.</p></div>
  <svg class="icon" style="top:292px" viewBox="0 0 46 46" fill="none" stroke="#fff" stroke-width="2"><circle cx="23" cy="14" r="9" stroke-dasharray="4 2"/><circle cx="23" cy="14" r="4"/><circle cx="11" cy="32" r="3"/><circle cx="23" cy="32" r="3"/><circle cx="35" cy="32" r="3"/><path d="M5 43v-4h12v4M17 43v-4h12v4M29 43v-4h12v4"/></svg>
  <div class="service" style="top:267px"><h3>Change management</h3><p>Veltrix works with clients to deliver bespoke change initiatives. Rigorous business analysis and risk management allows for successful change initiatives. We work with you throughout the complete process, to ensure that delivery is based on value. Transition phases are challenging aspects of change initiatives which is why our team manage all transitions and the risk they carry.</p></div>
  <svg class="icon" style="top:412px" viewBox="0 0 46 46" fill="none" stroke="#fff" stroke-width="2"><rect x="4" y="16" width="26" height="18" rx="1"/><path d="M1 38h32"/><circle cx="33" cy="12" r="7" stroke-dasharray="3 2"/><circle cx="33" cy="12" r="3"/></svg>
  <div class="service" style="top:396px"><h3>IT transformation</h3><p>Veltrix is widely experienced in a range of technologies. We help with the implementation of software provider or design and develop bespoke services. Covering front to back office the team specialises in full project lifecycle from feasibility through to implementation.</p></div>
  <svg class="icon" style="top:506px" viewBox="0 0 46 46" fill="none" stroke="#fff" stroke-width="2"><circle cx="11" cy="9" r="5"/><circle cx="30" cy="8" r="5" stroke-dasharray="3 2"/><rect x="6" y="18" width="30" height="18"/><path d="M12 30l6-6 5 4 8-7M10 42h24"/></svg>
  <div class="service" style="top:494px"><h3>Organisational structure</h3><p>Veltrix works with clients to improve resource capability and strategic partnerships. Acting as an extension of the HR function, we analyse business processes and ensure that our clients have the ability to manage changing workforce demands.</p></div>
</section>

<!-- Recruitment front -->
<section class="sheet sheet--recruit front">
  <div class="hero-photo" role="img" aria-label="Business people walking past financial charts"></div>
  <span class="word word--bold" style="left:294px;top:24px;font-size:40px">FIXED</span>
  <span class="word word--bold" style="left:294px;top:59px;font-size:40px">INCOME</span>
  <span class="word word--thin" style="left:188px;top:92px;font-size:52px">LEDGER</span>
  <span class="word word--thin" style="left:58px;top:140px;font-size:24px">WORKFLOW <b style="font-weight:700">MIS</b></span>
  <span class="word word--thin" style="left:128px;top:160px;font-size:24px">MANAGEMENT</span>
  <span class="word word--bold" style="left:338px;top:136px;font-size:64px">EQUITY</span>
  <span class="word word--thin" style="left:2px;top:192px;font-size:28px">TRADING PLATFORMS<b style="font-weight:700">XML</b></span>
  <div class="hero-band"></div>
  <p class="tagline">A partner who brings new and innovative ideas to the table, through extensive industry experience and knowledge. Veltrix will ensure you are prepared for growth.</p>
  <div class="logo"><span class="logo__mark"></span><span class="logo__name">VELTRIX</span></div>
  <h1 class="title" style="left:61px;top:400px"><span class="title__top">VELTRIX</span><span class="title__main">RECRUITMENT</span></h1>
  <div class="rcol" style="left:61px;top:474px;width:280px">
    <p>Veltrix is more than an ordinary recruitment service. Our experts work with clients to develop a HR strategy that maps current, and impending, organisational needs; using research to effectively benchmark. We are developing various talent communities that provide effective, and timely, recruitment solutions for our clients.</p>
    <p>Specialists in: Asset Management recruitment with a specialisation in I.T, Operations, Regulation and Change Management.</p>
    <p>Veltrix acts as an extension of your HR function, providing an end-to-end permanent and contingent talent acquisition solution, taking full accountability and ownership for the entire recruitment process, which includes:</p>
    <ul><li>Workforce Planning</li><li>Strategic Sourcing</li><li>Talent Engagement</li><li>Candidate Management</li><li>Weekly vacancy updates</li></ul>
  </div>
  <div class="rcol" style="left:356px;top:474px;width:258px">
    <p>We recognise that hiring can be a lengthy process, therefore we partner with you to ensure you only interview top quantile candidates, cutting out multiple meetings with multiple candidates. Giving hiring managers time back in their diaries to do their day jobs and reducing the time to hire. This is achieved by:</p>
    <ul><li>Understanding the roles, and partnering with you to build meaningful job descriptions</li><li>Candidates are fully screened and interviewed prior to presentation to you</li><li>Qualified shortlist of top 3 candidates</li><li>Support with interviews and we ensure the candidate has a positive experience</li></ul>
    <p>Veltrix recruitment partners with principal business consultants from Veltrix consultancy to ensure candidates are properly screened before presenting to our clients. This allows for our clients to focus on only interviewing the best on the market.</p>
  </div>
  <footer class="footer">
    <div class="logo"><span class="logo__mark"></span><span class="logo__name">VELTRIX</span></div>
    <span class="contact" style="left:368px;top:17px"><svg viewBox="0 0 12 12"><circle cx="6" cy="6" r="6" fill="#fff"/><path d="M6 3a2 2 0 0 0-2 2c0 1.5 2 4 2 4s2-2.5 2-4a2 2 0 0 0-2-2z" fill="#1b5aa2"/></svg>12 Harbor Lane, Sampleton, NJ 12345</span>
    <span class="contact" style="left:368px;top:37px"><svg viewBox="0 0 12 12"><circle cx="6" cy="6" r="6" fill="#fff"/><path d="M4 3l1 .2.5 1.5-.7.6a4 4 0 0 0 1.9 1.9l.6-.7 1.5.5L9 8c-.3.6-1 .9-1.7.6A6 6 0 0 1 3.4 4.7C3.1 4 3.4 3.3 4 3z" fill="#1b5aa2"/></svg>555-014-2290</span>
    <span class="contact" style="left:464px;top:37px"><svg viewBox="0 0 12 12"><circle cx="6" cy="6" r="6" fill="#fff"/><path d="M3 6l6-3-2 6-1.2-2z" fill="#1b5aa2"/></svg>hello@veltrix.co</span>
  </footer>
</section>

<!-- Services reverse B -->
<section class="sheet sheet--services-b services">
  <div class="services-photo" role="img" aria-label="Colleagues talking by an office window with rising arrow graphics"></div>
  <div class="logo"><span class="logo__mark"></span><span class="logo__name">VELTRIX</span></div>
  <div class="rule"></div>
  <svg class="icon" style="top:178px" viewBox="0 0 46 46" fill="none" stroke="#fff" stroke-width="2"><circle cx="23" cy="12" r="7"/><path d="M20 20h6M20 23h6"/><circle cx="9" cy="32" r="3"/><circle cx="23" cy="32" r="3"/><circle cx="37" cy="32" r="3"/><path d="M4 42c0-4 10-4 10 0M18 42c0-4 10-4 10 0M32 42c0-4 10-4 10 0"/></svg>
  <div class="service" style="top:150px"><h3 class="service__lead">Business Strategy</h3><p>Veltrix will help you create a business strategy tailored to your requirements. Ensuing each business process is defined and taken into account allows for a successful design. Creating and implementing an operating model that takes into account budget, resources, culture and your company's vision.</p></div>
  <svg class="icon" style="top:292px" viewBox="0 0 46 46" fill="none" stroke="#fff" stroke-width="2"><circle cx="23" cy="14" r="9" stroke-dasharray="4 2"/><circle cx="23" cy="14" r="4"/><circle cx="11" cy="32" r="3"/><circle cx="23" cy="32" r="3"/><circle cx="35" cy="32" r="3"/><path d="M5 43v-4h12v4M17 43v-4h12v4M29 43v-4h12v4"/></svg>
  <div class="service" style="top:267px"><h3>Change management</h3><p>Veltrix works with clients to deliver bespoke change initiatives. Rigorous business analysis and risk management allows for successful change initiatives. We work with you throughout the complete process, to ensure that delivery is based on value. Transition phases are challenging aspects of change initiatives which is why our team manage all transitions and the risk they carry.</p></div>
  <svg class="icon" style="top:412px" viewBox="0 0 46 46" fill="none" stroke="#fff" stroke-width="2"><rect x="4" y="16" width="26" height="18" rx="1"/><path d="M1 38h32"/><circle cx="33" cy="12" r="7" stroke-dasharray="3 2"/><circle cx="33" cy="12" r="3"/></svg>
  <div class="service" style="top:396px"><h3>IT transformation</h3><p>Veltrix is widely experienced in a range of technologies. We help with the implementation of software provider or design and develop bespoke services. Covering front to back office the team specialises in full project lifecycle from feasibility through to implementation.</p></div>
  <svg class="icon" style="top:506px" viewBox="0 0 46 46" fill="none" stroke="#fff" stroke-width="2"><circle cx="11" cy="9" r="5"/><circle cx="30" cy="8" r="5" stroke-dasharray="3 2"/><rect x="6" y="18" width="30" height="18"/><path d="M12 30l6-6 5 4 8-7M10 42h24"/></svg>
  <div class="service" style="top:494px"><h3>Organisational structure</h3><p>Veltrix works with clients to improve resource capability and strategic partnerships. Acting as an extension of the HR function, we analyse business processes and ensure that our clients have the ability to manage changing workforce demands.</p></div>
</section>

</body>
</html>
```